UX Design for Analytics Web Application

http://velqoranthe.com/
We are tech & consulting company with analytics products (web applications), located at Rio de Janeiro, Brazil.

We are searching a partner do develop UX for our products, i.e, aesthetics, usability, HTML/CSS.

Currently we have a product suite and the goal is to make a pilot re-design project with one of our products.

The product of interest is interactive webapp that aims at data analysis, significantly different from blogs, e-commerce or landing pages.

We do have a software development team but we lack an UX & HTML expert. Currently we use Bootstrap templates but the results are insatisfatory.

So, the project scope is, to develop the arts (UX, aesthetics, etc) along with the code/mockup (HTML/CSS) for one of our product (3 pages).

This is a pilot project and there's potential to rehire for our other products. Code quality is of importance.

More details and specification can be found in attached files.

Target Market(s)

Executives, managers & consultants

Industry/Entity Type

It Company

Coding

Coded - Design and coding required

Number of Pages Required

3 page

Font styles to use
Sans Serif

Requirements
Must have
• (see attached files, prefer the pptx version))
• -Responsive
Nice to have
• (see attached files, prefer the pptx version)
Should not have
• -Avoid Green, Red and Yellow colors. They have a meaning of good, bad and average in our products.

```html
<!DOCTYPE html>
<html lang="en">
<head>
<meta charset="utf-8">
<title>Velqor – Processes Dashboard</title>
<link href="https://fonts.googleapis.com/css2?family=Figtree:wght@400;500;600;700&display=swap" rel="stylesheet">
<style>
:root{
  --ink:#2f2f33;
  --muted:#5a5a60;
  --line:#d9d9dc;
  --page:#ececee;
  --white:#ffffff;
  --dark:#3d3d40;
  --navy:#34334d;
  --accent-deep:#5b3f8c;
  --accent-mid:#3f73b8;
  --accent-soft:#8a9bc4;
  --accent-flag:#4f86c6;
  --ring-a:#3f73b8;
  --ring-b:#7a5ca8;
  --ring-c:#8fb3df;
}
*{box-sizing:border-box;margin:0;padding:0}
html,body{width:1200px;height:1146px;overflow:hidden}
body{position:relative;background:var(--page);font-family:'Figtree',sans-serif;color:var(--ink)}
.abs{position:absolute}

.topbar{position:absolute;left:0;top:0;width:1200px;height:108px;background:var(--white);box-shadow:0 1px 3px rgba(0,0,0,.08)}
.menu-toggle{left:130px;top:32px}
.brand{display:flex;align-items:center;gap:8px}
.brand-dot{width:12px;height:12px;border-radius:50%;background:var(--navy)}
.brand-name{font-weight:700;font-size:34px;color:var(--muted);letter-spacing:-.5px}
.brand-tag{font-size:10px;font-weight:600;color:var(--ink);margin-left:20px;margin-top:-2px}
.topbar .brand-block{left:175px;top:22px}
.top-icons{left:878px;top:40px;display:flex;gap:48px}

.panel{position:absolute;background:var(--white);border:1px solid #dcdcdf}
.summary{left:111px;top:149px;width:330px;height:318px}
.summary-title{left:22px;top:64px;font-size:18px;font-weight:500}
.donut{left:223px;top:30px}
.donut-label{left:218px;top:120px;font-size:13px;width:108px;text-align:center}
.metric{left:20px;font-size:13px}
.metric .m1{color:var(--accent-deep)} .metric .m2{color:var(--accent-mid)} .metric .m3{color:var(--accent-soft)}
.bar{left:207px;height:15px}
.pct{font-size:13px}

.feed{left:111px;top:486px;width:330px;height:402px}
.feed-head{position:absolute;left:-1px;top:-1px;width:330px;height:35px;background:var(--dark);color:var(--white);display:flex;align-items:center;gap:14px;padding-left:20px;font-weight:700;font-size:14px}
.feed-item{position:absolute;left:26px;width:285px;height:116px}
.feed-item+.feed-item{border-top:1px solid var(--line)}
.avatar{position:absolute;left:8px;width:46px;height:46px;border-radius:50%;background:linear-gradient(135deg,#8d99a3,#4a4f58)}
.feed-date{position:absolute;left:72px;font-size:9.5px;color:var(--muted)}
.feed-text{position:absolute;left:72px;width:205px;font-size:11.5px;line-height:16px;color:var(--muted)}
.feed-name{position:absolute;left:72px;font-size:9px;font-weight:500}

.board{left:463px;top:148px;width:653px;height:740px}
.tool{position:absolute;top:17px;height:48px;border:1px solid #cfcfd3;display:flex;align-items:center;gap:9px;padding-left:16px;font-size:12px;color:var(--ink);white-space:nowrap}
.tool.primary{background:var(--dark);color:var(--white);border-color:var(--dark);padding-left:14px}

.card{position:absolute;width:295px;height:271px;border:1px solid #d6d6da;background:var(--white);overflow:hidden}
.card-media{position:absolute;left:0;top:0;width:100%;height:95px;background:linear-gradient(180deg,#4a4a68,#6b6478 55%,#3b3a52)}
.card-title{position:absolute;left:0;top:40px;width:100%;text-align:center;color:var(--white);font-size:18px;font-weight:500}
.card-flag{position:absolute;right:0;top:0}
.card-lead{position:absolute;left:43px;top:118px;font-size:19px;line-height:27px}
.card-bullet{position:absolute;left:16px;top:122px}
.card-note{position:absolute;left:44px;top:182px;font-size:13px;line-height:21px;color:var(--muted)}
.card-amount{position:absolute;left:189px;top:123px;width:88px;height:88px;border-radius:50%;background:var(--navy);color:var(--white);text-align:center;padding-top:14px;line-height:27px}
.card-amount .cur{font-size:22px;display:block}
.card-amount .num{font-size:28px}

.pager{position:absolute;top:686px;width:24px;height:24px;border:1px solid #c9c9cd;display:flex;align-items:center;justify-content:center;font-size:11px;background:var(--white)}
.pager.nav{background:var(--dark);border-color:var(--dark)}

.footer{position:absolute;left:0;top:932px;width:1200px;height:214px;background:var(--white)}
.footer .brand-block{left:532px;top:42px}
.footer .brand-name{font-size:30px}
.footer-rule{left:474px;top:136px;width:252px;border-top:1px solid #bdbdc1}
.footer-copy{left:0;top:160px;width:1200px;text-align:center;font-size:12px;color:var(--muted)}
</style>
</head>
<body>

<header class="topbar">
  <svg class="abs menu-toggle" width="26" height="22" viewBox="0 0 26 22"><path d="M1 2h24M1 11h24M1 20h24" stroke="#333" stroke-width="2"/></svg>
  <div class="abs brand-block">
    <div class="brand"><span class="brand-dot"></span><span class="brand-name">Velqor</span></div>
    <div class="brand-tag">Data, Insight &amp; Strategy</div>
  </div>
  <div class="abs top-icons">
    <svg width="28" height="30" viewBox="0 0 28 30" fill="none" stroke="#333" stroke-width="1.6"><path d="M5 22V13a9 9 0 0 1 18 0v9l3 3H2z"/><path d="M11 27a3 3 0 0 0 6 0M14 2v2"/></svg>
    <svg width="26" height="30" viewBox="0 0 26 30" fill="none" stroke="#333" stroke-width="1.6"><circle cx="13" cy="9" r="7"/><path d="M1 28c0-7 5-11 12-11s12 4 12 11z"/></svg>
    <svg width="30" height="30" viewBox="0 0 30 30" fill="none" stroke="#333" stroke-width="1.6"><circle cx="15" cy="15" r="5"/><path d="M13 2h4l1 4 3 1 3-2 3 3-2 3 1 3 4 1v4l-4 1-1 3 2 3-3 3-3-2-3 1-1 4h-4l-1-4-3-1-3 2-3-3 2-3-1-3-4-1v-4l4-1 1-3-2-3 3-3 3 2 3-1z"/></svg>
  </div>
</header>

<section class="panel summary">
  <div class="abs summary-title">14 Active Processes</div>
  <svg class="abs donut" width="80" height="80" viewBox="0 0 80 80">
    <circle cx="40" cy="40" r="36" fill="none" stroke="#eee" stroke-width="5"/>
    <circle cx="40" cy="40" r="36" fill="none" stroke="var(--ring-a)" stroke-width="5" stroke-dasharray="90 227" transform="rotate(-90 40 40)"/>
    <circle cx="40" cy="40" r="36" fill="none" stroke="var(--ring-b)" stroke-width="5" stroke-dasharray="72 227" stroke-dashoffset="-90" transform="rotate(-90 40 40)"/>
    <circle cx="40" cy="40" r="36" fill="none" stroke="var(--ring-c)" stroke-width="5" stroke-dasharray="65 227" stroke-dashoffset="-162" transform="rotate(-90 40 40)"/>
    <text x="40" y="45" text-anchor="middle" font-size="14" font-family="Figtree,sans-serif" fill="#2f2f33">72%</text>
  </svg>
  <div class="abs donut-label">CONCLUDED</div>

  <div class="abs metric" style="top:176px">31 millions &nbsp;<span class="m1">expent</span></div>
  <div class="abs bar" style="top:178px;width:103px;background:var(--accent-deep)"></div>

  <div class="abs metric" style="top:224px">with 2 millions of <span class="m2">gap</span></div>
  <div class="abs bar" style="top:226px;width:82px;background:var(--accent-mid)"></div>
  <div class="abs pct" style="left:296px;top:228px;color:var(--accent-mid)">6%</div>

  <div class="abs metric" style="top:272px">and 1.5 million of <span class="m3">negotiated</span></div>
  <div class="abs bar" style="top:274px;width:60px;background:var(--accent-soft)"></div>
  <div class="abs pct" style="left:274px;top:274px;color:var(--accent-soft)">5%</div>
</section>

<section class="panel feed">
  <div class="feed-head">
    <svg width="14" height="14" viewBox="0 0 14 14" fill="none" stroke="#fff" stroke-width="2"><path d="M2 6a6 6 0 0 1 6 6M2 1a11 11 0 0 1 11 11"/><circle cx="3" cy="11" r="1.5" fill="#fff" stroke="none"/></svg>
    ACTIVIY FEED
  </div>
  <div class="feed-item" style="top:38px">
    <div class="avatar" role="img" aria-label="Profile photo of Richard" style="top:18px"></div>
    <div class="feed-date" style="top:17px">30 MARCH,2017</div>
    <div class="feed-text" style="top:35px">There are many variations of passa of Lorem Ipsum.</div>
    <div class="feed-name" style="top:80px">RICHARD</div>
  </div>
  <div class="feed-item" style="top:155px">
    <div class="avatar" role="img" aria-label="Profile photo of Peter Prem" style="top:25px"></div>
    <div class="feed-date" style="top:25px">30 MARCH,2017</div>
    <div class="feed-text" style="top:43px">There are many variations of passa of Lorem Ipsum.</div>
    <div class="feed-name" style="top:88px">PETER PREM</div>
  </div>
  <div class="feed-item" style="top:269px">
    <div class="avatar" role="img" aria-label="Profile photo of Stanly" style="top:24px"></div>
    <div class="feed-date" style="top:25px">30 MARCH,2017</div>
    <div class="feed-text" style="top:43px">There are many variations of passa of Lorem Ipsum.</div>
    <div class="feed-name" style="top:88px">STANLY</div>
  </div>
</section>

<main class="panel board">
  <div class="tool" style="left:18px;width:196px">
    <svg width="12" height="12" viewBox="0 0 12 12" fill="none" stroke="#555" stroke-width="1.6"><circle cx="5" cy="5" r="4"/><path d="M8 8l3 3"/></svg>
    <span style="margin-left:10px">SEARCH</span>
  </div>
  <div class="tool" style="left:227px;width:130px">
    <svg width="18" height="16" viewBox="0 0 18 16" fill="none" stroke="#333" stroke-width="1.6"><path d="M4 1v13M1 11l3 3 3-3M9 2h8M9 6h6M9 10h4M9 14h2"/></svg>
    SORT BY
    <svg width="10" height="16" viewBox="0 0 10 16" fill="#333" style="margin-left:6px"><path d="M5 1l4 5H1zM5 15l4-5H1z"/></svg>
  </div>
  <div class="tool" style="left:366px;width:130px">
    <svg width="12" height="12" viewBox="0 0 12 12" fill="#333"><path d="M0 0h12L7 6v6L5 10V6z"/></svg>
    FILTER BY
    <svg width="10" height="16" viewBox="0 0 10 16" fill="#333"><path d="M5 1l4 5H1zM5 15l4-5H1z"/></svg>
  </div>
  <div class="tool primary" style="left:505px;width:130px">
    <svg width="11" height="11" viewBox="0 0 12 12" stroke="#fff" stroke-width="2.4"><path d="M6 0v12M0 6h12"/></svg>
    ADD PROCESS
  </div>

  <article class="card" style="left:18px;top:87px">
    <div class="card-media" role="img" aria-label="City skyline at dusk"></div>
    <div class="card-title">PROCESS BUY &nbsp;A DONUT</div>
    <svg class="card-flag" width="44" height="48" viewBox="0 0 44 48"><path d="M0 0h44v48A44 44 0 0 1 0 0z" fill="var(--accent-flag)"/><path d="M14 19l6 6 12-12" stroke="#fff" stroke-width="4" fill="none"/></svg>
    <svg class="card-bullet" width="18" height="18" viewBox="0 0 18 18"><circle cx="9" cy="9" r="9" fill="var(--accent-flag)"/><path d="M7 5l4 4-4 4" stroke="#fff" stroke-width="2" fill="none"/></svg>
    <div class="card-lead">14 Million<br>in expenses</div>
    <div class="card-note">Some Short free text<br>with links and 13,432<br>numbers</div>
    <div class="card-amount"><span class="cur">$</span><span class="num">568</span></div>
  </article>

  <article class="card" style="left:338px;top:87px">
    <div class="card-media" role="img" aria-label="Business people silhouettes by an office window"></div>
    <div class="card-title">PROCESS BUY &nbsp;A DONUT</div>
    <svg class="card-flag" width="44" height="48" viewBox="0 0 44 48"><path d="M0 0h44v48A44 44 0 0 1 0 0z" fill="var(--accent-flag)"/><path d="M14 19l6 6 12-12" stroke="#fff" stroke-width="4" fill="none"/></svg>
    <svg class="card-bullet" width="18" height="18" viewBox="0 0 18 18"><circle cx="9" cy="9" r="9" fill="var(--accent-flag)"/><path d="M7 5l4 4-4 4" stroke="#fff" stroke-width="2" fill="none"/></svg>
    <div class="card-lead">14 Million<br>in expenses</div>
    <div class="card-note">Some Short free text<br>with links and 13,432<br>numbers</div>
    <div class="card-amount"><span class="cur">$</span><span class="num">568</span></div>
  </article>

  <article class="card" style="left:18px;top:383px">
    <div class="card-media" role="img" aria-label="Aerial view of city streets"></div>
    <div class="card-title">PROCESS BUY &nbsp;A DONUT</div>
    <svg class="card-flag" width="44" height="48" viewBox="0 0 44 48"><path d="M0 0h44v48A44 44 0 0 1 0 0z" fill="var(--accent-flag)"/><path d="M14 19l6 6 12-12" stroke="#fff" stroke-width="4" fill="none"/></svg>
    <svg class="card-bullet" width="18" height="18" viewBox="0 0 18 18"><circle cx="9" cy="9" r="9" fill="var(--accent-flag)"/><path d="M7 5l4 4-4 4" stroke="#fff" stroke-width="2" fill="none"/></svg>
    <div class="card-lead">14 Million<br>in expenses</div>
    <div class="card-note">Some Short free text<br>with links and 13,432<br>numbers</div>
    <div class="card-amount"><span class="cur">$</span><span class="num">568</span></div>
  </article>

  <article class="card" style="left:338px;top:383px">
    <div class="card-media" role="img" aria-label="City skyline at dusk"></div>
    <div class="card-title">PROCESS BUY &nbsp;A DONUT</div>
    <svg class="card-flag" width="44" height="48" viewBox="0 0 44 48"><path d="M0 0h44v48A44 44 0 0 1 0 0z" fill="var(--accent-flag)"/><path d="M14 19l6 6 12-12" stroke="#fff" stroke-width="4" fill="none"/></svg>
    <svg class="card-bullet" width="18" height="18" viewBox="0 0 18 18"><circle cx="9" cy="9" r="9" fill="var(--accent-flag)"/><path d="M7 5l4 4-4 4" stroke="#fff" stroke-width="2" fill="none"/></svg>
    <div class="card-lead">14 Million<br>in expenses</div>
    <div class="card-note">Some Short free text<br>with links and 13,432<br>numbers</div>
    <div class="card-amount"><span class="cur">$</span><span class="num">568</span></div>
  </article>

  <div class="pager nav" style="left:433px"><svg width="8" height="10" viewBox="0 0 8 10" fill="none" stroke="#fff" stroke-width="1.6"><path d="M6 1L2 5l4 4"/></svg></div>
  <div class="pager" style="left:470px">1</div>
  <div class="pager" style="left:506px">2</div>
  <div class="pager" style="left:539px">3</div>
  <div class="pager" style="left:572px">4</div>
  <div class="pager nav" style="left:607px"><svg width="8" height="10" viewBox="0 0 8 10" fill="none" stroke="#fff" stroke-width="1.6"><path d="M2 1l4 4-4 4"/></svg></div>
</main>

<footer class="footer">
  <div class="abs brand-block">
    <div class="brand"><span class="brand-dot"></span><span class="brand-name">Velqor</span></div>
    <div class="brand-tag">Data, Insight &amp; Strategy</div>
  </div>
  <div class="abs footer-rule"></div>
  <div class="abs footer-copy">Copyrights &nbsp;@ 2017 All Rights Reserved</div>
</footer>

</body>
</html>
```